Website Redesign - We Need Your Magic!

Hello we are looking for you to help us re-design a high end and professional website for a high-end private school.

Here is the current site: http://www.ferndalecrest.com/

NOTE THIS IS DESIGN ONLY, NO CODING :)

The image they want to portray is that of high quality sports and education, in a creative "un-stiff" way.

Menu Bar: Horizontal

Look and Feel:

Site Colors: Dark green and a Gold yellow (logos are attached)

This site will represent a school so the look must be clean, bold, and classy. The site must have a very clean user interface, with things easily recognizable. Think simple.

The site should be visually appealing! If you come to me with templates, or a ton of text you will be out.

This site should be outside the box, we do not want boring, we do not want status quo. This site should instill excitement, innovation, and athletics.

So the main points again are:

1. High-end and classy look, with creative feel
2. Simple and clear navigation style
3. To cover the Junior and High School - Ferndale Crest College Schools

Think outside the box. We look forward to seeing what you come up with!!

Thank you for helping us create an amazing site for the school!

Industry/Entity Type

School

```html
<!DOCTYPE html>
<html lang="en">
<head>
<meta charset="utf-8">
<title>Ferndale Crest College Schools</title>
<link href="https://fonts.googleapis.com/css2?family=Arimo:wght@400;700&family=Montserrat:wght@500;600;700&display=swap" rel="stylesheet">
<style>
:root{
  --green:#0e5f30;
  --green-dark:#0b4a25;
  --gold:#c2a80f;
  --gold-text:#a8860e;
  --yellow:#e8c81f;
  --ink:#222;
  --line:#cfcfcf;
  --footer:#2b2b2b;
  --footer-base:#1e1e1e;
}
*{box-sizing:border-box;margin:0;padding:0}
html,body{width:905px;height:1200px;overflow:hidden}
body{position:relative;background:#fafafa;font-family:"Arimo",Arial,sans-serif;color:var(--ink);font-size:10.4px;line-height:1.32}
.abs{position:absolute}
.header{left:0;top:0;width:905px;height:118px;background:#f7f7f7}
.crest{left:78px;top:14px;width:66px;height:66px;border-radius:50%;background:var(--green)}
.site-name{left:170px;top:34px;font-family:"Montserrat",sans-serif;font-weight:600;font-size:19px;color:var(--green);white-space:nowrap}
.tagline{left:171px;top:73px;font-size:11px;color:#333;word-spacing:1px}
.contact{left:528px;top:33px;font-size:11px;color:#444;display:flex;gap:14px;align-items:center;white-space:nowrap}
.contact span{display:flex;align-items:center;gap:6px}
.search{left:525px;top:64px;width:304px;height:28px;display:flex}
.search-input{flex:1;border:1px solid #ccc;background:#fff;font-size:10px;color:#777;padding:7px 8px}
.search-btn{width:62px;background:var(--green-dark);color:#fff;font-size:9.5px;font-weight:700;display:flex;align-items:center;justify-content:center;gap:4px}
.nav{left:0;top:118px;width:905px;height:37px;background:var(--yellow);border-top:2px solid var(--green);display:flex;padding-left:64px;white-space:nowrap}
.nav a{font-family:"Montserrat",sans-serif;font-weight:600;font-size:11px;color:#2d2a10;text-decoration:none;padding:0 12px;line-height:35px;border-right:1px solid #c9ab12;flex:none}
.nav a:last-child{border-right:none}
.slider{left:0;top:155px;width:905px;height:296px;background:var(--green)}
.slide{top:16px;height:251px}
.s1{left:77px;width:253px;background:linear-gradient(135deg,#b98a4a,#5e4a2c 60%,#3f7d74)}
.s2{left:330px;width:268px;background:linear-gradient(180deg,#b8b2a4,#6f6a60 55%,#4a5a2e)}
.s3{left:598px;width:231px;background:linear-gradient(160deg,#5b7a2e,#8da24e 60%,#6f8e38)}
.arrow{top:116px;width:32px;height:32px;border-radius:50%;background:#111;display:flex;align-items:center;justify-content:center}
h2{font-family:"Arimo",sans-serif;font-weight:400;font-size:19px;color:var(--gold-text)}
.welcome{left:75px;top:480px;width:486px}
.lead{margin-top:10px;font-weight:700;color:var(--green);font-size:10.3px;line-height:1.5}
.welcome p.body{margin-top:12px}
.more{text-align:right;font-style:italic;font-weight:700;font-size:9.6px;position:relative;margin-top:8px}
.more::before{content:"";position:absolute;left:0;right:68px;top:50%;border-top:1px solid var(--line)}
.more span{background:#fafafa;padding-left:6px;padding-right:2px}
.head{left:75px;top:628px;width:486px}
.portrait{left:77px;top:663px;width:121px;height:141px;background:linear-gradient(180deg,#2f6b48,#c69a7e 55%,#d8cbb8)}
.head-text{left:211px;top:661px;width:350px}
.head-text p+p{margin-top:12px}
.head .more{margin-top:176px}
.col-title{display:flex;justify-content:space-between;align-items:center;border-bottom:1px solid var(--line);padding-bottom:4px}
.pager{display:flex;gap:2px}
.pager i{width:14px;height:14px;border:1px solid #ccc;background:#eee;display:block}
.events{left:78px;top:880px;width:225px}
.event{padding:10px 3px 10px;border-bottom:1px solid var(--line)}
.event:last-child{border-bottom:none}
.event .date{text-align:right;font-style:italic;font-weight:700;font-size:9.6px;color:var(--green);margin-bottom:4px}
.calendar{left:339px;top:880px;width:226px}
.calendar p{margin-top:9px;line-height:1.5;padding-left:2px}
.newsletter{left:602px;top:485px;width:228px;height:132px;background:var(--gold);padding:12px 16px}
.nl-title{display:flex;align-items:center;gap:10px;font-family:"Montserrat",sans-serif;font-weight:700;font-size:17px;color:#111}
.nl-text{color:#fff;font-size:9.6px;margin-top:10px}
.nl-form{display:flex;margin-top:10px;height:26px}
.nl-input{flex:1;background:#fff;font-size:10px;color:#555;padding:6px 7px}
.nl-go{width:38px;background:var(--green);color:#fff;font-size:12px;display:flex;align-items:center;justify-content:center}
.sports{left:605px;top:636px;width:225px}
.sports ul{list-style:none;margin-top:12px}
.sports li{display:flex;align-items:center;gap:8px;font-size:11px;height:21px}
.sports li i{width:8px;height:8px;border:1px solid #999;border-radius:50%}
.social{left:602px;top:795px;width:227px;height:247px;border:1px solid #bbb;background:#fff;overflow:hidden}
.social-bar{height:25px;background:#3f5a93;color:#fff;font-size:9.6px;display:flex;justify-content:space-between;align-items:center;padding:0 6px}
.social-bar b{font-size:11px}
.page-row{display:flex;gap:8px;padding:7px 5px;border-bottom:1px solid #ddd;height:50px}
.page-thumb{width:40px;height:36px;background:var(--green);border-radius:3px;flex:none}
.page-name{font-size:10px;color:#3b5998}
.like{font-size:7.5px;color:#333;margin-top:4px}
.post{display:flex;gap:8px;padding:8px 5px;height:96px;font-size:9px;border-bottom:1px solid #ddd}
.post .page-thumb{background:#d7d7d7}
.post-card{margin-top:6px;border:1px solid #ddd;padding:3px 6px;font-size:7.5px;color:#888}
.post-card b{color:#3b5998;font-weight:400;font-size:8.2px;display:block}
.fans{padding:4px 7px;font-size:8px}
.faces{display:flex;gap:4px;margin-top:4px}
.faces i{width:38px;height:38px;display:block}
.plugin{font-size:7px;color:#777;padding:3px 7px}
.footer{left:0;top:1072px;width:905px;height:102px;background:var(--footer);color:#fff}
.f-addr{left:105px;top:20px;width:190px}
.f-addr b{display:block;font-size:12px;margin-left:48px;white-space:nowrap}
.f-addr p{text-align:right;font-size:8.2px;margin-top:2px;line-height:1.4}
.f-addr a{display:block;text-align:right;color:#fff;font-size:7.8px;margin-top:6px}
.f-dl{left:394px;top:27px;font-size:10px}
.f-dl b,.f-conn b{font-size:12px;display:block;margin-bottom:8px}
.f-dl p{margin-top:3px}
.f-conn{left:677px;top:26px}
.badge{width:128px;height:38px;background:#fff;border:2px solid #ddd;display:flex;align-items:center;gap:7px;padding:0 8px;color:#3b5998;font-size:12px;font-weight:700}
.badge i{width:22px;height:22px;background:#3b5998;display:block}
.copyright{left:0;top:1174px;width:905px;height:26px;background:var(--footer-base);color:#ccc;font-size:10px;text-align:center;line-height:26px}
</style>
</head>
<body>
<header class="abs header">
  <div class="abs crest"></div>
  <div class="abs site-name">Ferndale Crest College Schools</div>
  <div class="abs tagline">Stepping Ahead in . Eduction . Culture &nbsp;. Sport . Life</div>
  <div class="abs contact">
    <span><svg width="11" height="11" viewBox="0 0 24 24"><path fill="#333" d="M6.6 10.8a15 15 0 006.6 6.6l2.2-2.2c.3-.3.7-.4 1-.2 1.1.4 2.3.6 3.6.6.6 0 1 .4 1 1V20c0 .6-.4 1-1 1A17 17 0 013 4c0-.6.4-1 1-1h3.5c.6 0 1 .4 1 1 0 1.3.2 2.5.6 3.6.1.3 0 .7-.2 1z"/></svg>0770100200 / 0770300400</span>
    <span><svg width="12" height="9" viewBox="0 0 12 9"><rect width="12" height="9" fill="#e6b84a"/><path d="M0 0l6 5 6-5" stroke="#fff" fill="none"/></svg>admin@ferndalecrest.com</span>
  </div>
  <div class="abs search">
    <div class="search-input">Search you any keyword</div>
    <div class="search-btn"><svg width="9" height="9" viewBox="0 0 10 10"><circle cx="4" cy="4" r="3" stroke="#fff" fill="none" stroke-width="1.4"/><path d="M6.2 6.2L9 9" stroke="#fff" stroke-width="1.4"/></svg>Search</div>
  </div>
</header>

<nav class="abs nav">
  <a>Home</a><a>About Us</a><a>Academics</a><a>Sports</a><a>Ferndale Crest College</a><a>Ferndale Crest College Primary School</a><a>Contact Us</a>
</nav>

<section class="abs slider">
  <div class="abs slide s1" role="img" aria-label="Pupils writing at their desks in a classroom"></div>
  <div class="abs slide s2" role="img" aria-label="Mountain bike race with riders on a dirt track"></div>
  <div class="abs slide s3" role="img" aria-label="Hockey players running on a grass field"></div>
  <div class="abs arrow" style="left:15px"><svg width="10" height="10" viewBox="0 0 10 10"><path d="M7 1L3 5l4 4" stroke="#f2d21b" stroke-width="2.2" fill="none"/></svg></div>
  <div class="abs arrow" style="left:860px"><svg width="10" height="10" viewBox="0 0 10 10"><path d="M3 1l4 4-4 4" stroke="#f2d21b" stroke-width="2.2" fill="none"/></svg></div>
</section>

<section class="abs welcome">
  <h2>Welcome to Ferndale Crest College</h2>
  <p class="lead">Welcome to Ferndale Crest Group of Schools where our School Motto is ‘Concordia’ meaning Togetherness. We aim to work together in every aspect of School life, from academics to sport.</p>
  <p class="body">Ferndale Crest College opened on 14th February 1983 and occupies 120 ha of land amidst the low hills of the Marlow Hills, 8km west of Eastvale. This location encourages focus on School life away from the distractions and hustle and bustle of the larger towns.</p>
  <div class="more"><span>More Details.</span></div>
</section>

<section class="abs head">
  <h2>Headmaster's Welcome Note</h2>
  <div class="more"><span>More Details.</span></div>
</section>
<div class="abs portrait" role="img" aria-label="Portrait of the headmaster"></div>
<div class="abs head-text">
  <p><b>Welcome to Ferndale Crest College.</b>&nbsp; Here at the College we aim to encourage each pupil to be a self-confident, well-rounded individual.&nbsp; We aim to propel them to the highest level of achievement in both academics and extra- curricular activities to provide them with the life skills they will need when they leave the College and to prepare them to be of value to society.</p>
  <p>The College is a warm community which lives out high standards and is rightly proud of its achievements.&nbsp; We are a small enough School for each pupil to be known well, but large enough to offer a wide range of subjects and experience.</p>
</div>

<section class="abs events">
  <div class="col-title"><h2>Upcoming Events</h2><div class="pager"><i></i><i></i></div></div>
  <div class="event"><div class="date">Mon 04 Aug</div><p>When an unknown printer took a galley of type and scra mbled it specimen book.</p></div>
  <div class="event"><div class="date">Mon 04 Aug</div><p>When an unknown printer took a galley of type and scra mbled it specimen book.</p></div>
</section>

<section class="abs calendar">
  <div class="col-title"><h2>School Calender</h2><div class="pager"><i></i><i></i></div></div>
  <p>Begins: Tuesday 14th January<br>1st Fixture Free: Friday 31st January – Monday 3rd February<br>Half-Term: Thursday 20th February – Tuesday 25th February<br>2nd Fixture Free: Friday 14th March – Monday 17th March<br>Term Ends: Thursday &nbsp;10th April</p>
</section>

<aside class="abs newsletter">
  <div class="nl-title"><svg width="25" height="25" viewBox="0 0 25 25"><circle cx="12.5" cy="12.5" r="12.5" fill="#0e5f30"/><rect x="7" y="9" width="11" height="8" fill="#fff"/><path d="M7 9l5.5 4.5L18 9" stroke="#0e5f30" fill="none"/></svg>NEWSLETTER</div>
  <p class="nl-text">If you would like to be added to the list of parents that receive the School Newsletter,</p>
  <div class="nl-form"><div class="nl-input">Email Address</div><div class="nl-go">GO</div></div>
</aside>

<section class="abs sports">
  <h2>Sports Announcements</h2>
  <ul><li><i></i>Rugby</li><li><i></i>Hockey Boys</li><li><i></i>Soccer</li><li><i></i>Hockey Girls</li><li><i></i>Basketball Girls</li></ul>
</section>

<aside class="abs social">
  <div class="social-bar"><span>Find us on Friendbook</span><b>Friendbook</b></div>
  <div class="page-row"><div class="page-thumb"></div><div><div class="page-name">Campus Chatter</div><div class="like">✓ Like &nbsp; You like this.</div></div></div>
  <div class="post"><div class="page-thumb"></div><div><div class="page-name">Campus Chatter</div><p>"The idea of a culinary contest one either."</p><div class="post-card"><b>Social Media Campaign</b>www.campuschatter.com<br>Homely ChefPlus cookbook.</div></div></div>
  <div class="fans">30,821 people like <b>Campus Chatter</b>.
    <div class="faces"><i style="background:#8a6a55"></i><i style="background:#6d5a48"></i><i style="background:#7f95a8"></i><i style="background:#5a5f7a"></i><i style="background:#9a6e5c"></i></div>
  </div>
  <div class="plugin">Friendbook social plugin</div>
</aside>

<footer class="abs footer">
  <svg class="abs" style="left:105px;top:22px" width="32" height="42" viewBox="0 0 32 42"><path d="M16 0a16 16 0 0116 16c0 12-16 26-16 26S0 28 0 16A16 16 0 0116 0z" fill="#f0a21a"/><circle cx="16" cy="15" r="5" fill="#2b2b2b"/></svg>
  <div class="abs f-addr"><b>Ferndale Crest College</b><p>12 Marlow Lane,<br>Eastvale 4021</p><a>Click here to see the directions &gt;&gt;</a></div>
  <div class="abs f-dl"><b>Download</b><p>Registration Form</p><p>2nd Term 2014 Termly Calendar</p></div>
  <div class="abs f-conn"><b>Connect With Us</b><div class="badge"><i></i>Friendbook</div></div>
</footer>
<div class="abs copyright">Copyright © 2014 Ferndale Crest. All Rights Reserved.</div>
</body>
</html>
```